Business cards to launch an education platform

Hi,
I am looking at having new business cards designed.
I am a startup, developing a web platform for schools and university, the education world. It's an online assessment system.
I would like a card that looks classy, and that is using the colors and the font of my logo.

I have attached:
1) my logo
2) A business card that I have designed quickly so you can have all the information required in the card, but I really don't like it.
3) The font that I am using (Lato Regular) to design my web platform
4) Some screenshots of my web platform so you can have a look at the style that I have.

Target Market(s)

Major market: Education system: Schools and university
Minor markets: Business in general

Industry/Entity Type

Business

Contact Information for Business Card

Clara Fenwick
Director

M: 0437 518 902
E: clara.fenwick@amberLoomSystems.com.au

Requirements
Must have
• The colors of my logo

```html
<!DOCTYPE html>
<html lang="en">
<head>
<meta charset="utf-8">
<title>Amber Loom Systems – Business Card</title>
<link rel="stylesheet" href="https://fonts.googleapis.com/css2?family=Arimo:wght@400;700&family=Lato:wght@400&display=swap">
<style>
  :root {
    --backdrop: #e9e7e3;
    --card-white: #ffffff;
    --navy: #0b4a86;
    --navy-deep: #08386a;
    --sky: #1fa2dc;
    --brand-blue: #1b5fa8;
    --text-light: #ffffff;
  }
  * { margin: 0; padding: 0; box-sizing: border-box; }
  html, body {
    width: 1200px;
    height: 902px;
    overflow: hidden;
    background: var(--backdrop);
  }
  .card {
    position: absolute;
    left: 100px;
    top: 166px;
    width: 1000px;
    height: 572px;
    background: var(--card-white);
    box-shadow: 0 14px 40px rgba(0, 0, 0, 0.18);
    overflow: hidden;
  }
  .card-wave {
    position: absolute;
    inset: 0;
    width: 100%;
    height: 100%;
  }
  .brand {
    position: absolute;
    left: 150px;
    top: 84px;
    display: flex;
    align-items: center;
    gap: 20px;
  }
  .brand-mark {
    width: 60px;
    height: 60px;
    background: var(--brand-blue);
  }
  .brand-name {
    font-family: "Lato", sans-serif;
    font-weight: 400;
    font-size: 42px;
    letter-spacing: 2px;
    color: var(--brand-blue);
    white-space: nowrap;
  }
  .holder {
    position: absolute;
    left: 60px;
    top: 438px;
    color: var(--text-light);
    font-family: "Arimo", sans-serif;
  }
  .holder-name {
    font-weight: 700;
    font-size: 44px;
    line-height: 1.05;
    word-spacing: 8px;
    white-space: nowrap;
  }
  .holder-role {
    font-weight: 700;
    font-size: 30px;
    line-height: 1.3;
  }
  .divider {
    position: absolute;
    left: 430px;
    top: 430px;
    width: 2px;
    height: 104px;
    background: var(--text-light);
    opacity: 0.85;
  }
  .contacts {
    position: absolute;
    left: 452px;
    top: 442px;
    list-style: none;
    font-family: "Arimo", sans-serif;
    font-size: 23px;
    color: var(--text-light);
  }
  .contact-item {
    display: flex;
    align-items: center;
    gap: 12px;
    height: 42px;
    white-space: nowrap;
  }
  .contact-phone { word-spacing: 6px; }
  .contact-icon {
    width: 22px;
    height: 22px;
    flex: none;
  }
</style>
</head>
<body>
  <article class="card">
    <svg class="card-wave" viewBox="0 0 1000 572" preserveAspectRatio="none" aria-hidden="true">
      <path d="M0,372 C260,392 520,300 740,170 C840,112 920,84 1000,78 L1000,572 L0,572 Z" fill="var(--sky)"/>
      <path d="M0,402 C270,418 540,330 760,200 C850,148 930,118 1000,112 L1000,572 L0,572 Z" fill="var(--navy)"/>
      <path d="M0,572 L0,520 C300,540 700,480 1000,400 L1000,572 Z" fill="var(--navy-deep)" opacity="0.35"/>
    </svg>

    <div class="brand">
      <span class="brand-mark"></span>
      <span class="brand-name">Amber Loom Systems</span>
    </div>

    <div class="holder">
      <p class="holder-name">Clara Fenwick</p>
      <p class="holder-role">Director</p>
    </div>

    <span class="divider"></span>

    <ul class="contacts">
      <li class="contact-item contact-phone">
        <svg class="contact-icon" viewBox="0 0 24 24" aria-label="Phone">
          <rect x="1" y="1" width="22" height="22" rx="3" fill="var(--text-light)"/>
          <path d="M7 6h3l1 4-2 1c1 2 2 3 4 4l1-2 4 1v3c0 1-1 2-2 2C10 19 5 14 5 8c0-1 1-2 2-2z" fill="var(--navy)"/>
        </svg>
        <span>0437 518 902</span>
      </li>
      <li class="contact-item">
        <svg class="contact-icon" viewBox="0 0 24 24" aria-label="Email">
          <rect x="1" y="1" width="22" height="22" rx="3" fill="var(--text-light)"/>
          <rect x="5" y="7" width="14" height="10" fill="none" stroke="var(--navy)" stroke-width="1.6"/>
          <path d="M5 7l7 6 7-6" fill="none" stroke="var(--navy)" stroke-width="1.6"/>
        </svg>
        <span>clara.fenwick@amberLoomSystems.com.au</span>
      </li>
    </ul>
  </article>
</body>
</html>
```